New Fun, Positive, energised looking Business Card Needed for High Achiever Coach

I am looking for a two sided full colour business card. I am self employed and have recently re branded my 1-2-1 work re-vitalising high achievers. My target client base for these cards is therefore high achievers - usually aged 40 -55, they are often entrepreneurs, CEO or work in banking and finance and 2/3 are male. I work with them on 90 day or 6 month coaching programs to help them live their success in a healthier, more sustainable and fulfiiled way. They pay for this privately so though they are corporate types the cards need not look 'corporate'. I want to portray the idea of transformation, vitality and re-connecting.
You can get a feel for the look I like on my new website: morvenlisk.co.uk
I want to use this logo with strapline (Re-Vitalising High Achievers) (I purchased off Logoharbor) and font/ colours (the turquoise and green).
Details to include on the card:
www.morvenlisk.co.uk
+44 7915 302618
morven@morvenlisk.co.uk
skype: morvenlisk
I'd also like to include:
Do you struggle to switch off? Want to be healthier and feel fitter? Want closer relationships? More clarity over the direction you are headed? I can help you do these things using integrated mind-body techniques. Visit morvenlisk.co.uk TODAY to apply for a FREE Breakthrough session.
BUT if that is too much text for a card I am open to advice/ammendments.
Updates
Thanks for your design - I am considering them. PLease change the wording to :

```html
<!DOCTYPE html>
<html lang="en">
<head>
<meta charset="utf-8">
<title>Morven Lisk – Business Card</title>
<link rel="stylesheet" href="https://fonts.googleapis.com/css2?family=Open+Sans:wght@400;700&family=Tinos&display=swap">
<style>
  :root {
    --bg: #e6e7ec;
    --white: #ffffff;
    --teal: #00a5c8;
    --teal-text: #14a9cc;
    --green: #5fba6e;
    --shadow: rgba(40, 50, 70, 0.18);
  }
  * { margin: 0; padding: 0; box-sizing: border-box; }
  html, body {
    width: 1200px;
    height: 987px;
    overflow: hidden;
    background: var(--bg);
  }
  .canvas {
    position: relative;
    width: 1200px;
    height: 987px;
    display: flex;
    align-items: center;
    justify-content: center;
    gap: 40px;
  }
  .card {
    position: relative;
    width: 540px;
    height: 310px;
    border-radius: 24px;
    overflow: hidden;
    box-shadow: 0 10px 28px var(--shadow);
  }
  .card-front { background: var(--white); }
  .front-waves {
    position: absolute;
    inset: 0;
    width: 100%;
    height: 100%;
  }
  .wave-green { fill: var(--green); }
  .wave-teal { fill: var(--teal); }

  .brand {
    position: absolute;
    left: 34px;
    top: 46px;
    display: flex;
    align-items: center;
    gap: 10px;
    font-family: "Open Sans", sans-serif;
    font-weight: 700;
    font-size: 34px;
    line-height: 1;
    color: var(--teal-text);
  }
  .brand-dot {
    width: 16px;
    height: 16px;
    border-radius: 50%;
    background: var(--green);
    flex: none;
  }

  .contact-list {
    position: absolute;
    right: 24px;
    bottom: 12px;
    list-style: none;
    font-family: "Tinos", serif;
    font-size: 18px;
    color: var(--white);
    text-align: right;
  }
  .contact-item {
    display: flex;
    align-items: center;
    justify-content: flex-end;
    gap: 7px;
    line-height: 24px;
  }
  .contact-icon {
    width: 14px;
    height: 14px;
    flex: none;
  }
  .contact-icon * { fill: none; stroke: var(--white); stroke-width: 1.6; }
  .contact-icon .solid { fill: var(--white); stroke: none; }
  .chat-dot {
    width: 13px;
    height: 13px;
    border-radius: 50%;
    background: var(--white);
    flex: none;
  }

  .card-back {
    background: var(--green);
    display: flex;
    align-items: center;
    justify-content: center;
    padding: 0 26px;
  }
  .pitch {
    font-family: "Open Sans", sans-serif;
    font-size: 17.5px;
    line-height: 1.3;
    color: var(--white);
    text-align: center;
  }
  .pitch-questions { margin-bottom: 10px; }
  .pitch strong { font-weight: 700; }
</style>
</head>
<body>
<main class="canvas">

  <section class="card card-front" aria-label="Business card front">
    <svg class="front-waves" viewBox="0 0 540 310" preserveAspectRatio="none" aria-hidden="true">
      <path class="wave-green" d="M0,95 C70,160 250,178 540,166 L540,310 L0,310 Z"/>
      <path class="wave-teal" d="M0,116 C75,176 260,188 540,176 L540,310 L0,310 Z"/>
    </svg>

    <div class="brand"><span class="brand-dot"></span>Morven Lisk</div>

    <ul class="contact-list">
      <li class="contact-item">
        <svg class="contact-icon" viewBox="0 0 14 14" aria-hidden="true">
          <circle cx="7" cy="7" r="6"/>
          <path class="solid" d="M4.6,3.8 L6,3.6 L6.6,5.4 L5.8,6 C6.2,7 7,7.8 8,8.2 L8.6,7.4 L10.4,8 L10.2,9.4 C7,9.6 4.4,7 4.6,3.8 Z"/>
        </svg>
        +44 7915 302618
      </li>
      <li class="contact-item">
        <svg class="contact-icon" viewBox="0 0 14 14" aria-hidden="true">
          <rect x="1" y="3" width="12" height="9" rx="1"/>
          <path d="M1.5,3.5 L7,8 L12.5,3.5"/>
        </svg>
        morven@morvenlisk.co.uk
      </li>
      <li class="contact-item">
        <svg class="contact-icon" viewBox="0 0 14 14" aria-hidden="true">
          <circle cx="7" cy="7" r="6"/>
          <ellipse cx="7" cy="7" rx="2.6" ry="6"/>
          <path d="M1,7 H13"/>
        </svg>
        www.morvenlisk.co.uk
      </li>
      <li class="contact-item">
        <span class="chat-dot" aria-hidden="true"></span>
        morvenlisk
      </li>
    </ul>
  </section>

  <section class="card card-back" aria-label="Business card back">
    <div class="pitch">
      <p class="pitch-questions">
        Do you struggle to switch off?<br>
        Want to be healthier and feel fitter?<br>
        Want closer relationships?<br>
        More clarity over the direction you are headed?<br>
        I can help you do these things using integrated<br>
        mind-body techniques.
      </p>
      <p class="pitch-call">
        Visit <strong>morvenlisk.co.uk</strong> TODAY to apply for a<br>
        FREE Breakthrough session.
      </p>
    </div>
  </section>

</main>
</body>
</html>
```